Machining Business Order Thank You Insert

I am looking for a business style card to include with orders that I ship. The card needs to thank the recipient for their order, and encourage them to leave a review. The card should include my business name and contact information and have an area to hand write a message.

I mainly sale on Craftlane and my own website. We are a machining an manufacturing business that are in the sale of mostly metal machined and 3d printed plastic products.

The front of the card should include the following:
Logo: (attached)
Snapgram: https://www.snapgram.example/kelvomill/
Friendsbook: https://www.friendsbook.example/KelvoMill
Website: https://www.kelvomill.example/

The back of the card needs an area to write a message

Industry/Entity Type

3D Printing, Machining, Craftlane

Contact Information for Business Card

Black or white front, white back to write a personal message

Font styles to use
Sans Serif

Colors

Designer to choose colors to be used in the design.

Requirements
Must have
• Encourage a review, social media info

```html
<!DOCTYPE html>
<html lang="en">
<head>
<meta charset="utf-8">
<title>KelvoMill Order Thank You Card</title>
<link rel="stylesheet" href="https://fonts.googleapis.com/css2?family=Bebas+Neue&family=Lato:wght@400;700&display=swap">
<style>
  :root {
    --backdrop: #2a2a2a;
    --card-white: #ffffff;
    --card-back: #f8faf7;
    --brand-orange: #f05a2a;
    --brand-grey: #6c6c6e;
    --faint-mark: #f1e6e0;
    --card-shadow: #111111;
  }
  html, body {
    margin: 0;
    padding: 0;
    width: 1075px;
    height: 1200px;
    overflow: hidden;
    background: var(--backdrop);
  }
  .canvas {
    position: relative;
    width: 1075px;
    height: 1200px;
  }
  .card {
    position: absolute;
    left: 206px;
    width: 663px;
    height: 395px;
    box-shadow: 3px 3px 0 var(--card-shadow);
  }
  .card svg { display: block; width: 100%; height: 100%; }
  .card--front { top: 187px; background: var(--card-white); }
  .card--back { top: 637px; background: var(--card-back); }
  .brand-name {
    font-family: "Lato", sans-serif;
    font-weight: 400;
    fill: var(--brand-grey);
    letter-spacing: 7px;
  }
  .contact-line {
    font-family: "Lato", sans-serif;
    font-weight: 400;
    fill: var(--card-white);
  }
  .contact-icon { fill: var(--card-white); }
  .thank-you {
    font-family: "Bebas Neue", sans-serif;
    fill: var(--card-white);
  }
  .wave--grey { fill: var(--brand-grey); }
  .wave--orange { fill: var(--brand-orange); }
  .wave--gap { fill: var(--card-white); }
  .back-mark {
    font-family: "Lato", sans-serif;
    font-weight: 400;
    fill: var(--faint-mark);
    letter-spacing: 14px;
  }
</style>
</head>
<body>
<main class="canvas">
  <section class="card card--front" aria-label="Card front">
    <svg viewBox="0 0 738 439" xmlns="http://www.w3.org/2000/svg">
      <text class="brand-name" x="40" y="258" font-size="32">KELVOMILL</text>

      <path class="wave--grey" d="M0,305 C90,330 210,330 348,233 C260,305 150,352 0,338 Z"/>
      <path class="wave--orange" d="M0,350 C110,372 200,362 285,322 C400,262 520,162 650,152 C700,148 725,153 738,159 L738,439 L0,439 Z"/>
      <path class="wave--gap" d="M70,396 C240,402 370,276 462,212 C555,150 620,132 672,130 C590,134 515,162 432,218 C325,292 225,382 70,396 Z"/>
      <path class="wave--orange" d="M85,392 C250,395 380,270 470,210 C560,150 620,138 662,133 C590,132 520,160 440,215 C330,290 230,380 85,392 Z"/>

      <g class="contact">
        <text class="contact-line" x="678" y="278" font-size="19" text-anchor="end">www.kelvomill.example</text>
        <circle class="contact-icon" cx="697" cy="272" r="11"/>
        <text class="contact-line" x="678" y="308" font-size="19" text-anchor="end">www.snapgram.example/kelvomill</text>
        <circle class="contact-icon" cx="697" cy="302" r="11"/>
        <text class="contact-line" x="678" y="338" font-size="19" text-anchor="end">www.friendsbook.example/KelvoMill</text>
        <circle class="contact-icon" cx="697" cy="331" r="11"/>
      </g>

      <text class="thank-you" x="703" y="413" font-size="50" text-anchor="end">THANK YOU FOR YOUR ORDER</text>
    </svg>
  </section>

  <section class="card card--back" aria-label="Card back, space for a handwritten message">
    <svg viewBox="0 0 738 439" xmlns="http://www.w3.org/2000/svg">
      <text class="back-mark" x="369" y="245" font-size="84" text-anchor="middle">KELVOMILL</text>
    </svg>
  </section>
</main>
</body>
</html>
```